Mara Penrith Copywriter Website

I am starting a new business as a freelance copywriter. Trying to set up the website for my business is proving to be too technical for me. I would like a simple, clean website using primarily black and white. I have attached the logo I would like used. I would like the menu icons to be Home, Services, Portfolio, Blog, Contact. I would like my mobile phone number (0412 583 906) and email address (mara.penrith.copywriter@fernmail.test) used in the header of the site. I need the site to be easily manageable and inter-changeable for me to be able to move things around and add images, etc with ease.

I would like the home page to be a static page with space for an image of myself somewhere (I haven't had this taken as yet), an area to put a bit about myself and my business, and also somewhere to include social media icons/links. Again, I would like the whole website and home page to be easily managed so that I can add/delete things with ease.

I would like the image of the typewriter used in the website somewhere also please.

Coding

Coded - Design and coding required

Number of Pages Required

5+ page

Font styles to use
Sans Serif
Script

Colors
fdf0f6

Requirements
Must have
• The logo provided
• Ability to change page contents easily
• Ability to add social media icons as needed
Nice to have
• Use of the typewriter image
Should not have
• Complicated pages that are not easily editable

```html
<!DOCTYPE html>
<html lang="en">
<head>
<meta charset="utf-8">
<title>Mara Penrith Copywriter</title>
<link href="https://fonts.googleapis.com/css2?family=Lato:ital,wght@0,300;0,400;0,700;0,900;1,400&family=Cinzel:wght@700&display=swap" rel="stylesheet">
<style>
:root{
  --black:#000;
  --ink:#111;
  --white:#fff;
  --grey-text:#555;
  --muted:#999;
  --line:#ddd;
  --soft:#f2f2f2;
  --blush:#fdf0f6;
  --shadow:#f3d9e3;
}
*{margin:0;padding:0;box-sizing:border-box}
html,body{width:1200px;height:3814px;overflow:hidden}
body{font-family:'Lato',sans-serif;color:var(--ink);background:var(--white);position:relative}
section,header,footer{position:relative;width:1200px}
.abs{position:absolute}

/* top bar */
.topbar{height:51px;background:var(--black);color:var(--white);font-size:15px;font-weight:700}
.topbar .contact{position:absolute;top:0;height:51px;display:flex;align-items:center;gap:12px}
.topbar .social{position:absolute;right:120px;top:18px;display:flex;gap:15px}
.topbar .social span{width:14px;height:14px;border-radius:50%;background:var(--white);display:block}

/* nav */
.nav{height:114px;background:var(--white);border-bottom:1px solid var(--line)}
.brand{position:absolute;left:76px;top:30px;width:340px;height:56px;display:flex;align-items:center;gap:14px;font-size:24px;font-weight:700;color:var(--ink)}
.brand .mark{width:30px;height:30px;background:var(--blush);display:block}
.menu{position:absolute;top:0;left:520px;height:114px;display:flex;align-items:center;font-size:18px;color:#444}
.menu a{text-decoration:none;color:inherit;position:absolute;white-space:nowrap}
.menu a.active{color:var(--black);font-weight:700}
.menu a.active::after{content:"";position:absolute;left:50%;bottom:-46px;margin-left:-10px;border:10px solid transparent;border-bottom-color:var(--black)}
.search{position:absolute;left:1075px;top:32px;width:50px;height:50px;border-radius:50%;background:#f4f4f4;display:flex;align-items:center;justify-content:center}

/* hero */
.hero{height:575px;background:linear-gradient(180deg,#4a4542 0%,#3a3532 45%,#2a2522 100%);color:var(--white);text-align:center}
.hero .kicker{position:absolute;top:155px;width:100%;font-size:22px;letter-spacing:1px}
.hero h1{position:absolute;top:192px;width:100%;font-family:'Cinzel',serif;font-size:48px;font-weight:700;letter-spacing:1px}
.hero .lede{position:absolute;top:258px;width:100%;font-size:15px;font-style:italic;font-weight:700;line-height:31px}
.btn{position:absolute;left:503px;top:346px;width:195px;height:66px;background:var(--white);color:var(--black);border:3px solid var(--black);outline:2px solid var(--white);font-size:20px;font-weight:700;display:flex;align-items:center;justify-content:center;letter-spacing:.5px}

/* welcome */
.welcome{height:564px}
.welcome .portrait-shadow{position:absolute;left:90px;top:77px;width:471px;height:430px;background:var(--shadow)}
.welcome .portrait{position:absolute;left:76px;top:63px;width:471px;height:430px;background:linear-gradient(135deg,#7a9a6c,#cdd5c6 55%,#e8e1d8)}
h2.title{font-size:36px;font-weight:300;color:var(--ink)}
h2.title b{font-weight:900}
.welcome h2{position:absolute;left:613px;top:62px}
.welcome p{position:absolute;left:613px;top:133px;width:525px;font-size:13px;line-height:24.3px;color:var(--grey-text)}

/* services */
.services{height:727px}
.services .panel{position:absolute;left:0;top:0;width:547px;height:727px;background:var(--black);color:var(--white)}
.services h2{position:absolute;left:81px;top:58px;color:var(--white)}
.services .intro{position:absolute;left:81px;top:135px;width:420px;font-size:15px;font-style:italic;line-height:29px}
.service{position:absolute;left:76px;width:420px}
.service svg{position:absolute;left:0;top:0}
.service h3{position:absolute;left:92px;top:0;font-size:21px;font-weight:400}
.service p{position:absolute;left:92px;top:36px;width:300px;font-size:13px;line-height:25px}
.services .photo{position:absolute;left:547px;top:0;width:653px;height:727px;background:linear-gradient(135deg,#c9c6c0,#a9a6a1 50%,#6d6b69)}

/* portfolio */
.portfolio{height:605px;text-align:center}
.portfolio h2{position:absolute;top:60px;width:100%}
.filters{position:absolute;top:140px;left:0;width:100%;font-size:15px;color:#666}
.filters span{position:absolute;top:0;height:40px;line-height:40px}
.filters .on{background:var(--black);color:var(--white);border-radius:20px;width:72px;font-weight:700}
.work{position:absolute;top:239px;background:var(--white);box-shadow:0 0 8px rgba(0,0,0,.18);padding:10px}
.work .img{width:100%;height:168px}
.work .cap{font-size:20px;margin-top:20px;color:#222;letter-spacing:.5px}

/* blog */
.blog{height:676px;background:var(--soft)}
.blog h2{position:absolute;top:58px;width:100%;text-align:center}
.post{position:absolute;top:137px;width:331px;height:455px;background:var(--white);box-shadow:0 0 8px rgba(0,0,0,.15)}
.post .img{position:absolute;left:10px;top:8px;width:311px;height:208px}
.post .month{position:absolute;left:18px;top:183px;background:var(--black);color:var(--white);font-size:13px;font-weight:700;padding:0 9px;height:31px;line-height:31px}
.post .day{position:absolute;left:18px;top:219px;width:66px;height:38px;background:#ddd;color:var(--white);font-size:18px;font-weight:700;line-height:38px;text-align:center}
.post .by{position:absolute;left:96px;top:228px;font-size:13px;font-style:italic;color:#555}
.post h3{position:absolute;left:22px;top:278px;font-size:18px;font-weight:700}
.post p{position:absolute;left:22px;top:318px;width:290px;font-size:13px;line-height:25px;color:#aaa}
.post .more{position:absolute;left:22px;top:390px;font-size:14px;font-weight:700;border-bottom:1px solid #999;padding-bottom:3px;display:flex;align-items:center;gap:8px}

/* footer */
.footer{height:404px;background:var(--black);color:var(--white);text-align:center}
.footer .brand-foot{position:absolute;top:72px;width:100%;font-size:26px;font-weight:700}
.footer p{position:absolute;top:168px;width:100%;font-size:15px;line-height:31px}
.footer .cta{position:absolute;top:244px;width:100%;font-size:15px;font-weight:700;display:flex;justify-content:center;align-items:center;gap:14px}
.footer .social{position:absolute;top:312px;left:0;width:100%}
.footer .social span{position:absolute;width:46px;height:46px;border-radius:50%;background:var(--white)}
.copyright{height:98px;background:var(--black);border-top:1px solid #333;color:var(--white);font-size:13px;text-align:center;line-height:98px}
.copyright b{font-weight:900}
</style>
</head>
<body>

<header class="topbar">
  <div class="contact" style="left:81px">
    <svg width="16" height="16" viewBox="0 0 24 24"><path d="M6.6 10.8a15 15 0 0 0 6.6 6.6l2.2-2.2a1 1 0 0 1 1-.25 11 11 0 0 0 3.6.6 1 1 0 0 1 1 1V20a1 1 0 0 1-1 1A17 17 0 0 1 3 4a1 1 0 0 1 1-1h3.5a1 1 0 0 1 1 1 11 11 0 0 0 .6 3.6 1 1 0 0 1-.25 1z" fill="#fff"/></svg>
    <span>0412 583 906</span>
  </div>
  <div class="contact" style="left:263px">
    <svg width="18" height="14" viewBox="0 0 18 14"><rect x="0" y="0" width="18" height="14" fill="#fff"/><path d="M0 0l9 7 9-7" stroke="#000" stroke-width="1.5" fill="none"/></svg>
    <span>mara.penrith.copywriter@fernmail.test</span>
  </div>
  <div class="social" aria-label="Social links"><span></span><span></span><span></span></div>
</header>

<nav class="nav">
  <div class="brand"><span class="mark"></span>Mara Penrith Copywriter</div>
  <div class="menu">
    <a class="active" style="left:14px">Home</a>
    <a style="left:121px">Services</a>
    <a style="left:243px">Portfolio</a>
    <a style="left:365px">Blog</a>
    <a style="left:446px">Contact</a>
  </div>
  <div class="search"><svg width="20" height="20" viewBox="0 0 20 20"><circle cx="8" cy="8" r="6" stroke="#333" stroke-width="2" fill="none"/><path d="M12.5 12.5l5 5" stroke="#333" stroke-width="2"/></svg></div>
</nav>

<section class="hero" role="img" aria-label="Desk with a typewriter and glasses, dimmed">
  <div class="kicker">I LOVE TO COPYWRITE</div>
  <h1>I AM MARA PENRITH</h1>
  <div class="lede">A wonderful serenity has taken possession of my entire soul, like these sweet mornings of<br>spring which I enjoy with my whole heart</div>
  <div class="btn">CONTACT US</div>
</section>

<section class="welcome">
  <div class="portrait-shadow"></div>
  <div class="portrait" role="img" aria-label="Portrait of the copywriter relaxing at an outdoor desk"></div>
  <h2 class="title">Welcome to <b>MARA PENRITH</b></h2>
  <p>Lorem Ipsum is simply dummy text of the printing and typesetting industry. Lorem Ipsum has been the industry's standard dummy text ever since the 1500s, when an unknown printer took a galley of type and scrambled it to make a type specimen book. It has survived not only five centuries, but also the leap into electronic typesetting, remaining essentially unchanged. It was popularised in the 1960s with the release of Tracemark sheets containing Lorem Ipsum passages, and more recently with desktop publishing software like Quillset Layout including versions of Lorem Ipsum.Lorem ipsum dolor sit amet, consectetur adipiscing elit, sed do eiusmod tempor incididunt ut labore et dolore magna aliqua. Ut enim ad minim veniam, quis nostrud exercitation ullamco laboris nisi ut aliquip ex ea commodo consequat. Duis aute irure dolor in reprehenderit in voluptate velit esse cillum dolore eu fugiat nulla pariatur. Excepteur sint occaecat cupidatat non proident.</p>
</section>

<section class="services">
  <div class="panel">
    <h2 class="title">Our <b>SERVICES</b></h2>
    <div class="intro">Lorem Ipsum is simply dummy text of the printing and typesetting industry.</div>

    <div class="service" style="top:231px">
      <svg width="52" height="52" viewBox="0 0 52 52" fill="none" stroke="#fff" stroke-width="2.5"><rect x="6" y="10" width="30" height="36" rx="3"/><path d="M12 20h18M12 28h18M12 36h10"/><path d="M44 6l4 4-16 16-5 1 1-5z"/></svg>
      <h3>Blogging</h3>
      <p>Lorem Ipsum is simply dummy text of the printing and typesetting industry Ipsum.</p>
    </div>
    <div class="service" style="top:356px">
      <svg width="52" height="52" viewBox="0 0 52 52" fill="none" stroke="#fff" stroke-width="2.5"><rect x="6" y="8" width="40" height="28" rx="3"/><path d="M20 36v8M32 36v8M14 46h24M14 16h24M14 22h24M14 28h14"/></svg>
      <h3>Blogging</h3>
      <p>Lorem Ipsum is simply dummy text of the printing and typesetting industry Ipsum.</p>
    </div>
    <div class="service" style="top:480px">
      <svg width="52" height="52" viewBox="0 0 52 52" fill="none" stroke="#fff" stroke-width="2.5"><circle cx="26" cy="26" r="6"/><circle cx="10" cy="10" r="4"/><circle cx="42" cy="10" r="4"/><circle cx="10" cy="42" r="4"/><circle cx="42" cy="42" r="4"/><path d="M13 13l8 8M39 13l-8 8M13 39l8-8M39 39l-8-8"/></svg>
      <h3>Blogging</h3>
      <p>Lorem Ipsum is simply dummy text of the printing and typesetting industry Ipsum.</p>
    </div>
    <div class="service" style="top:595px">
      <svg width="52" height="52" viewBox="0 0 52 52" fill="none" stroke="#fff" stroke-width="2.5"><rect x="10" y="6" width="36" height="40" rx="2"/><path d="M10 14H4v28a4 4 0 0 0 8 0"/><rect x="16" y="12" width="24" height="8"/><path d="M16 26h24M16 32h24M16 38h16"/></svg>
      <h3>Blogging</h3>
      <p>Lorem Ipsum is simply dummy text of the printing and typesetting industry Ipsum.</p>
    </div>
  </div>
  <div class="photo" role="img" aria-label="Hand writing in a notebook beside a laptop, glasses and coffee"></div>
</section>

<section class="portfolio">
  <h2 class="title">Our <b>PORTFOLIO</b></h2>
  <div class="filters">
    <span class="on" style="left:369px">All</span>
    <span style="left:486px">Story</span>
    <span style="left:572px">Reading</span>
    <span style="left:666px">Motion</span>
    <span style="left:773px">Inspiration</span>
  </div>
  <div class="work" style="left:130px;width:269px"><div class="img" role="img" aria-label="Stack of newspapers" style="background:linear-gradient(135deg,#e8e8e8,#9a9a9a)"></div></div>
  <div class="work" style="left:432px;width:336px"><div class="img" role="img" aria-label="People working on laptops" style="background:linear-gradient(135deg,#b0603a,#d9c7b8 55%,#6e6a66)"></div><div class="cap">READING</div></div>
  <div class="work" style="left:796px;width:272px"><div class="img" role="img" aria-label="Newspapers and a coffee cup" style="background:linear-gradient(135deg,#d8dadc,#8e9194)"></div></div>
</section>

<section class="blog">
  <h2 class="title">Recent <b>BLOG</b></h2>

  <article class="post" style="left:79px">
    <div class="img" role="img" aria-label="Person reading at a desk" style="background:linear-gradient(135deg,#d7d3cf,#8d8a86)"></div>
    <div class="month">August</div><div class="day">28</div>
    <div class="by">By : Dane Holloway</div>
    <h3>Trust is at the heart of change</h3>
    <p>Lorem Ipsum is simply dummy text of the printing and typesetting industry Ipsum.</p>
    <div class="more">READ MORE <svg width="18" height="12" viewBox="0 0 18 12" fill="none" stroke="#111" stroke-width="2"><path d="M2 1l5 5-5 5M9 1l5 5-5 5"/></svg></div>
  </article>
  <article class="post" style="left:435px">
    <div class="img" role="img" aria-label="Hands writing next to a laptop" style="background:linear-gradient(135deg,#ecebea,#b5b0aa)"></div>
    <div class="month">August</div><div class="day">29</div>
    <div class="by">By : Dane Holloway</div>
    <h3>Trust is at the heart of change</h3>
    <p>Lorem Ipsum is simply dummy text of the printing and typesetting industry Ipsum.</p>
    <div class="more">READ MORE <svg width="18" height="12" viewBox="0 0 18 12" fill="none" stroke="#111" stroke-width="2"><path d="M2 1l5 5-5 5M9 1l5 5-5 5"/></svg></div>
  </article>
  <article class="post" style="left:790px">
    <div class="img" role="img" aria-label="Person with a laptop on the beach" style="background:linear-gradient(180deg,#c9d3da,#ddd5c6 55%,#b8a78c)"></div>
    <div class="month">August</div><div class="day">30</div>
    <div class="by">By : Dane Holloway</div>
    <h3>Trust is at the heart of change</h3>
    <p>Lorem Ipsum is simply dummy text of the printing and typesetting industry Ipsum.</p>
    <div class="more">READ MORE <svg width="18" height="12" viewBox="0 0 18 12" fill="none" stroke="#111" stroke-width="2"><path d="M2 1l5 5-5 5M9 1l5 5-5 5"/></svg></div>
  </article>
</section>

<footer class="footer">
  <div class="brand-foot">Mara Penrith Copywriter</div>
  <p>Lorem Ipsum is simply dummy text of the printing and typesetting industry. Lorem Ipsum<br>has been the industry's standard dummy text ever since the 1500s,</p>
  <div class="cta">CONTACT US <svg width="34" height="12" viewBox="0 0 34 12" fill="none" stroke="#fff" stroke-width="2"><path d="M0 6h32M27 1l5 5-5 5"/></svg></div>
  <div class="social" aria-label="Social links">
    <span style="left:518px"></span><span style="left:577px"></span><span style="left:635px"></span>
  </div>
</footer>

<div class="copyright">Copyright © <b>MARA PENRITH</b> - 2018 . All Right Reserved</div>

</body>
</html>
```